Typography of the cover "Watch the tide turning"

We would like to improve the presentation of a book cover: presentation and typography of the authors and of the title. Image of the cover is available in two versions (with or without sky), joined with the texts (joined files): Mathis Corvenot Watched the turning tide Romance Editions Murlane

Industry/Entity Type

Publishing

Colors

Designer to choose colors to be used in the design.

Requirements
Must have
• Provided picture (with or without sky)

```html
<!DOCTYPE html>
<html lang="en">
<head>
<meta charset="utf-8">
<title>Watch the tide turning — Mathis Corvenot</title>
<link rel="stylesheet" href="https://fonts.googleapis.com/css2?family=Montserrat:wght@700;800&family=Stardos+Stencil:wght@700&display=swap">
<style>
  :root {
    --sky-top: #ebebea;
    --sky-mid: #c9c9c8;
    --haze: #8d8f90;
    --city-dark: #2a2b2c;
    --city-deep: #0f1011;
    --ink: #151515;
    --white: #ffffff;
    --red-deep: #58130f;
    --red-mid: #8f1c1a;
    --red-bright: #d52127;
    --outline: #ffffff;
  }
  * { margin: 0; padding: 0; box-sizing: border-box; }
  html, body { width: 810px; height: 1200px; overflow: hidden; background: var(--sky-top); }
  .cover {
    position: relative;
    width: 810px;
    height: 1200px;
    overflow: hidden;
  }
  .cover__photo {
    position: absolute;
    inset: 0;
    background: linear-gradient(180deg,
      var(--sky-top) 0%,
      var(--sky-mid) 42%,
      var(--haze) 62%,
      var(--city-dark) 82%,
      var(--city-deep) 100%);
  }
  .cover__author {
    position: absolute;
    top: 160px;
    left: 0;
    width: 100%;
    text-align: center;
    font-family: "Montserrat", sans-serif;
    font-weight: 800;
    font-size: 38px;
    letter-spacing: 0.14em;
    color: var(--ink);
  }
  .cover__title {
    position: absolute;
    top: 0;
    left: 0;
    width: 810px;
    height: 1200px;
  }
  .cover__title text {
    font-family: "Stardos Stencil", serif;
    font-weight: 700;
    font-size: 160px;
    stroke: var(--outline);
    stroke-width: 7px;
    stroke-linejoin: round;
    paint-order: stroke fill;
  }
  .cover__genre {
    position: absolute;
    top: 686px;
    left: 0;
    width: 100%;
    text-align: center;
    font-family: "Montserrat", sans-serif;
    font-weight: 800;
    font-size: 33px;
    letter-spacing: 0.14em;
    color: var(--white);
  }
  .cover__publisher {
    position: absolute;
    top: 1058px;
    left: 0;
    width: 100%;
    text-align: center;
    font-family: "Montserrat", sans-serif;
    font-weight: 700;
    font-size: 20px;
    letter-spacing: 0.14em;
    color: var(--white);
  }
</style>
</head>
<body>
  <main class="cover">
    <div class="cover__photo" role="img" aria-label="Black and white aerial photograph of a dense city skyline fading upward into a pale grey misty sky, with vertical motion blur"></div>

    <p class="cover__author">MATHIS CORVENOT</p>

    <svg class="cover__title" viewBox="0 0 810 1200" aria-label="Watch the tide turning">
      <text x="68" y="344" textLength="692" lengthAdjust="spacingAndGlyphs" fill="var(--red-deep)">WATCH THE</text>
      <text x="212" y="496" textLength="420" lengthAdjust="spacingAndGlyphs" fill="var(--red-mid)">TIDE</text>
      <text x="96" y="648" textLength="636" lengthAdjust="spacingAndGlyphs" fill="var(--red-bright)">TURNING</text>
    </svg>

    <p class="cover__genre">ROMAN</p>

    <p class="cover__publisher">EDITIONS MURLANE</p>
  </main>
</body>
</html>
```